Executive Business Card for Healthcare Company [Need Today]

I need a business card design for a healthcare company. The only branding the company has thus far is a logo. The cards will be utilized by company executives. The design I envision will be vibrant and appealing but with a corporate feel. They shouldn't be too casual or playful. I would like to complete this project TODAY if possible.

Target Market(s)

Healthcare vendors, other executives in healthcare and pharmaceuticals

Industry/Entity Type

Pharmaceutical

Contact Information for Business Card

See attachment

Font styles to use
Serif
Sans Serif

Colors

Designer to choose colors to be used in the design.

```html
<!DOCTYPE html>
<html lang="en">
<head>
<meta charset="utf-8">
<title>Meridane Therapeutics – Business Card</title>
<link href="https://fonts.googleapis.com/css2?family=Arimo:wght@400;700&display=swap" rel="stylesheet">
<style>
  :root {
    --bg: #ecebe8;
    --card-dark: #1d1d1f;
    --card-light: #ffffff;
    --teal: #2fbfc9;
    --green: #63c698;
    --ink: #222222;
    --grey: #8a8a8a;
  }
  * { margin: 0; padding: 0; box-sizing: border-box; }
  html, body {
    width: 1200px; height: 900px; overflow: hidden;
    background: var(--bg);
    font-family: "Arimo", Arial, sans-serif;
  }
  .stage { position: relative; width: 1200px; height: 900px; }
  .card {
    position: absolute; left: 320px; width: 560px; height: 320px;
    box-shadow: 0 6px 18px rgba(0,0,0,0.18);
    overflow: hidden;
  }
  .card--front { top: 100px; background: var(--card-dark); }
  .card--back  { top: 480px; background: var(--card-light); }

  .brand { position: absolute; display: flex; align-items: center; gap: 18px; }
  .brand__circle {
    width: 78px; height: 78px; border-radius: 50%;
    border: 3px solid var(--green); flex: none;
  }
  .brand__name {
    font-size: 30px; font-weight: 400; color: var(--teal);
    letter-spacing: 0.5px; line-height: 1;
  }
  .card--front .brand { left: 50%; top: 50%; transform: translate(-50%, -50%); }
  .card--back .brand { left: 44px; top: 34px; }
  .card--back .brand__circle { width: 70px; height: 70px; }
  .card--back .brand__name { font-size: 26px; }

  .person { position: absolute; left: 44px; top: 150px; }
  .person__name {
    font-size: 21px; font-weight: 700; color: var(--teal); letter-spacing: 0.8px;
  }
  .person__title { font-size: 15px; color: var(--ink); margin-top: 3px; }

  .contacts { position: absolute; left: 44px; top: 212px; list-style: none; }
  .contacts li {
    display: flex; align-items: center; gap: 6px;
    font-size: 15px; color: var(--ink); line-height: 21px;
  }
  .contacts svg { width: 15px; height: 15px; flex: none; }

  .company {
    position: absolute; right: 30px; top: 160px; text-align: right;
    font-size: 12.5px; color: var(--ink); line-height: 16px;
  }
  .company__name { color: var(--green); font-weight: 700; letter-spacing: 0.4px; }

  .band { position: absolute; left: 0; bottom: 0; width: 100%; height: 16px; display: flex; }
  .band__teal { flex: 0 0 68%; background: var(--teal); }
  .band__green { flex: 1; background: var(--green); }
</style>
</head>
<body>
<main class="stage">
  <section class="card card--front" aria-label="Card front">
    <div class="brand">
      <span class="brand__circle"></span>
      <span class="brand__name">Meridane Therapeutics</span>
    </div>
  </section>

  <section class="card card--back" aria-label="Card back">
    <div class="brand">
      <span class="brand__circle"></span>
      <span class="brand__name">Meridane Therapeutics</span>
    </div>

    <div class="person">
      <p class="person__name">DANIEL MOREAU</p>
      <p class="person__title">Senior Director of Marketing</p>
    </div>

    <ul class="contacts">
      <li>
        <svg viewBox="0 0 16 16" aria-hidden="true"><circle cx="8" cy="8" r="7" fill="none" stroke="#63c698" stroke-width="1.2"/><path d="M4.5 9.5h7v1.5h-7z M5.5 6.5c0-1 1-1.5 2.5-1.5s2.5.5 2.5 1.5v1h-5z" fill="#63c698"/></svg>
        555-210-4837
      </li>
      <li>
        <svg viewBox="0 0 16 16" aria-hidden="true"><circle cx="8" cy="8" r="7" fill="none" stroke="#63c698" stroke-width="1.2"/><rect x="5.8" y="4" width="4.4" height="8" rx="0.8" fill="none" stroke="#63c698" stroke-width="1.1"/></svg>
        555-318-6042
      </li>
      <li>
        <svg viewBox="0 0 16 16" aria-hidden="true"><circle cx="8" cy="8" r="7" fill="none" stroke="#63c698" stroke-width="1.2"/><rect x="4.3" y="5.3" width="7.4" height="5.4" fill="none" stroke="#63c698" stroke-width="1.1"/><path d="M4.3 5.5 8 8.4l3.7-2.9" fill="none" stroke="#63c698" stroke-width="1.1"/></svg>
        dmoreau@meridanerx.com
      </li>
    </ul>

    <address class="company" style="font-style:normal">
      <p class="company__name">MERIDANE THERAPEUTICS, LLC</p>
      <p>118 Linden Avenue</p>
      <p>Fairview, GA 30000</p>
    </address>

    <div class="band"><span class="band__teal"></span><span class="band__green"></span></div>
  </section>
</main>
</body>
</html>
```